Easy Marinade Labels for Butchery Store

Need a set of labels designed for a Butchery Shop. They will sit in the top left corner of the packets as a triangle (7cm each side). Easy because the only major requirement is the label name and some small text saying "Please ask in store to see spec sheet for ingredients". Extra points for finding a fun way to incorporate the logo and/or images of food (garlic bulbs, chilli, spices ect) to enhance the label. List of Marinade Names below: GarlicPepper Mint & RosemarySatayBBQChilli Plum & GingerSundried Tomato & BasilBuffaloHoney SoyHoi-SinPer PeriSpicy CajunTeriyakiBlack Bean Ive also attached the logo and an example of how the label might sit on a packet of meat. Thanks

Target Market(s)

Butchery Deli Shop Customers

Industry/Entity Type

Food Store

Font styles to use
Serif
Sans Serif
Decorative
Other font styles liked:
• Fun font that isn't a generic Quellbrix Font?

Colors

Designer to choose colors to be used in the design.

Requirements
Must have
• Product Name
• Small text saying "Please ask in store to see spec sheet for ingredients"
Nice to have
• Photos of ingredients that would match that type of marinade - Chilli, Garlic, Spices.
• Fenly Oak Logo - not essential if it doesn't look good on the label / doesn't fit.

```html
<!DOCTYPE html>
<html lang="en">
<head>
<meta charset="utf-8">
<title>Buffalo Marinade Label</title>
<link rel="stylesheet" href="https://fonts.googleapis.com/css2?family=Caveat+Brush&family=Signika:wght@700&display=swap">
<style>
  :root {
    --page: #ffffff;
    --frame-yellow: #eaff1a;
    --chilli-red: #c8141a;
    --deep-red: #7a0d0f;
    --sauce-brown: #4a1a14;
    --crumb-orange: #c8733d;
    --label-white: #ffffff;
  }
  html, body {
    margin: 0;
    padding: 0;
    width: 1200px;
    height: 900px;
    overflow: hidden;
    background: var(--page);
  }
  .canvas {
    position: relative;
    width: 1200px;
    height: 900px;
  }
  .label {
    position: absolute;
    left: 0;
    top: 0;
    width: 1200px;
    height: 900px;
  }
  .label-frame {
    fill: var(--frame-yellow);
  }
  .product-name {
    font-family: "Caveat Brush", cursive;
    font-size: 82px;
    fill: var(--label-white);
    stroke: #2a0a08;
    stroke-width: 1.5px;
    paint-order: stroke;
    letter-spacing: 0.02em;
  }
  .ingredients-note {
    font-family: "Signika", sans-serif;
    font-weight: 700;
    font-size: 22px;
    fill: var(--label-white);
  }
</style>
</head>
<body>
<main class="canvas">
  <svg class="label" viewBox="0 0 1200 900" xmlns="http://www.w3.org/2000/svg">
    <defs>
      <linearGradient id="food-tones" x1="0" y1="0" x2="1" y2="0.3">
        <stop offset="0" stop-color="var(--sauce-brown)"/>
        <stop offset="0.2" stop-color="var(--chilli-red)"/>
        <stop offset="0.5" stop-color="var(--chilli-red)"/>
        <stop offset="0.68" stop-color="var(--sauce-brown)"/>
        <stop offset="0.85" stop-color="var(--crumb-orange)"/>
        <stop offset="1" stop-color="#8a4a2a"/>
      </linearGradient>
      <linearGradient id="base-shade" x1="0" y1="0" x2="0" y2="1">
        <stop offset="0.75" stop-color="#000" stop-opacity="0"/>
        <stop offset="1" stop-color="var(--deep-red)" stop-opacity="0.6"/>
      </linearGradient>
    </defs>

    <polygon class="label-frame" points="624,170 1106,652 142,652"/>

    <g class="food-photo" role="img" aria-label="Photo of red chilli peppers and crumbed buffalo chicken wings">
      <polygon points="624,181 1090,644 158,644" fill="url(#food-tones)"/>
      <polygon points="624,181 1090,644 158,644" fill="url(#base-shade)"/>
    </g>

    <text class="product-name" x="630" y="486" text-anchor="middle" textLength="250" lengthAdjust="spacingAndGlyphs">BUFFALO</text>
    <text class="ingredients-note" x="625" y="623" text-anchor="middle" textLength="745" lengthAdjust="spacing">PLEASE ASK IN STORE TO SEE SPEC SHEET FOR INGREDIENTS</text>
  </svg>
</main>
</body>
</html>
```